Website for a Psychologist in Private Practice

I need a cool web design for my website: www.drkalvoric.com. I would like it to look professional. Keep all the current content and add: Space for video; radio spots (see Silver Cedar Tunes Logo below for those); Quick Inquiry; Friendora link; 5 star rating on Rivo; a map; reviews from former patients. I am open to suggestions.

Target Market(s)

Those seeking individual and marital counseling.

Industry/Entity Type

Mental Health

Number of Pages Required

1 page

Font styles to use
Sans Serif
Other font styles liked:
• I'm open but no hard to read script

Requirements
Must have
• All the content on my home page with link for video and radio spots. List services and degrees and expertices (pics not necessary).
Nice to have
• A video of me and radio conversations (logo of Silver Cedar Tunes radio attached).
Should not have
• Cartoons, comedy, etc.... I don't need pictures of services (marital, depression, etc...) Just list those.

```html
<!DOCTYPE html>
<html lang="en">
<head>
<meta charset="utf-8">
<title>Dr. Mara L. Kalvoric – Clinical Psychologist</title>
<link rel="stylesheet" href="https://fonts.googleapis.com/css2?family=Arimo:wght@400;700&family=Playball&display=swap">
<style>
:root{
  --gold:#c9a936;
  --gold-soft:#d4b94e;
  --grey-circle:#8e8e8e;
  --panel:#f3f3f3;
  --text:#4f4f4f;
  --ink:#1d1d1d;
  --footer:#333333;
  --footer-text:#9a9a9a;
  --white:#ffffff;
}
*{margin:0;padding:0;box-sizing:border-box}
html,body{width:763px;height:1200px;overflow:hidden;background:var(--white)}
body{position:relative;font-family:"Arimo",Arial,sans-serif;color:var(--text)}
.abs{position:absolute}
.hero{left:0;top:0;width:763px;height:305px;background:linear-gradient(180deg,#6d6455 0%,#8a7a5e 38%,#5b4a36 62%,#3b2a1e 100%)}
.nav{top:13px;left:0;width:763px;display:flex;justify-content:center;gap:30px;font-size:11.5px;color:var(--white);letter-spacing:.2px}
.nav .active{color:var(--gold)}
.hero-name{top:70px;width:763px;text-align:center;font-family:"Playball",cursive;font-size:42px;color:var(--gold-soft)}
.hero-role{top:151px;width:763px;text-align:center;font-size:19px;color:var(--white)}
.hero-license{top:179px;width:763px;text-align:center;font-size:11.5px;color:var(--white)}
.services{left:0;top:305px;width:763px;height:311px;background:var(--panel)}
.portrait{left:282px;top:205px;width:199px;height:199px;border-radius:50%;background:#e8e4dc;padding:7px;box-shadow:0 2px 4px rgba(0,0,0,.08)}
.portrait div{width:100%;height:100%;border-radius:50%;background:radial-gradient(circle at 50% 40%,#e9cfa4 0%,#c8a56f 35%,#3f6a8d 75%,#2f5c36 100%)}
.svc{width:80px;height:80px;border-radius:50%;background:var(--grey-circle);display:flex;align-items:center;justify-content:center}
.svc.gold{background:var(--gold)}
.svc-label{font-size:13.6px;color:var(--gold);line-height:20px}
.right{text-align:right}
.about-title{top:640px;width:763px;text-align:center;font-family:"Playball",cursive;font-size:25px;color:var(--ink)}
.about-title span{color:var(--gold)}
.about-text{left:90px;top:686px;width:584px;text-align:center;font-size:9px;line-height:14.6px;color:var(--text)}
.read-more{top:750px;width:763px;text-align:center;font-size:9.5px;color:var(--ink)}
.audio{left:79px;width:318px;height:93px;border:1px solid #dcdcdc;background:var(--white)}
.audio .photo{position:absolute;left:0;top:0;width:92px;height:92px;background:linear-gradient(160deg,#e6cf9c,#b98f5c 45%,#3c6690 80%,#2e5a33)}
.audio .play{position:absolute;left:99px;top:13px;width:16px;height:16px;border-radius:50%;background:var(--gold)}
.audio .by{position:absolute;left:118px;top:11px;font-size:8.5px;color:#8c8c8c}
.audio .title{position:absolute;left:118px;top:22px;font-size:9px;color:var(--ink)}
.audio .wave{position:absolute;left:99px;top:40px;width:209px;height:34px;background:repeating-linear-gradient(90deg,#cfcfcf 0 1.5px,transparent 1.5px 3.5px);-webkit-mask:linear-gradient(180deg,transparent 0,#000 20%,#000 80%,transparent 100%)}
.audio .time{position:absolute;left:299px;top:54px;font-size:5.5px;background:var(--gold);color:var(--white);padding:1px 2px}
.audio .plays{position:absolute;right:6px;bottom:6px;font-size:6.5px;color:#9a9a9a}
.monitor{left:446px;top:782px;width:268px;height:184px;background:#1f1f1f;border-radius:4px 4px 0 0}
.screen{left:454px;top:792px;width:251px;height:142px;background:linear-gradient(120deg,#e8d789,#d9c46c 55%,#c6ae57)}
.chin{left:446px;top:943px;width:268px;height:23px;background:linear-gradient(#e6e6e6,#bdbdbd);border-radius:0 0 4px 4px}
.stand{left:535px;top:966px;width:92px;height:34px;background:linear-gradient(#d0d0d0,#f2f2f2);clip-path:polygon(20% 0,80% 0,100% 100%,0 100%)}
.footer{left:0;top:1014px;width:763px;height:186px;background:var(--footer)}
.f-head{font-family:"Playball",cursive;font-size:13px;color:var(--gold)}
.f-list{list-style:none;font-size:9px;color:var(--footer-text);line-height:20px}
.f-list li:first-child{color:var(--white)}
.f-contact{font-size:9px;color:var(--footer-text);line-height:14.5px}
.badge{border-radius:6px;background:#4a4a4a}
.rule{left:50px;top:1166px;width:664px;height:1px;background:#4b4b4b}
.copy{left:50px;top:1177px;font-size:9px;color:var(--white)}
.copy span{color:var(--gold)}
.social{right:49px;top:1177px;font-size:9px;color:var(--gold);display:flex;gap:10px}
</style>
</head>
<body>

<div class="abs hero" role="img" aria-label="Beach at sunset with palm fronds"></div>
<nav class="abs nav"><span class="active">. HOME</span><span>. SESSIONS</span><span>. RESOURCES</span><span>. BIO</span><span>. CONTACT</span></nav>
<h1 class="abs hero-name">Dr. Mara L. Kalvoric</h1>
<p class="abs hero-role">CLINICAL PSYCHOLOGIST</p>
<p class="abs hero-license">California # PSY20581</p>

<section class="abs services">
  <svg class="abs" style="left:0;top:0" width="763" height="311" aria-hidden="true">
    <g fill="none" stroke="#cfcfcf" stroke-width="2" stroke-dasharray="2 4">
      <line x1="190" y1="0" x2="190" y2="28"/>
      <line x1="574" y1="0" x2="574" y2="28"/>
      <path d="M199 63 Q230 130 272 153 Q320 190 381 196 Q442 190 490 153 Q532 130 563 63"/>
    </g>
  </svg>
</section>

<div class="abs portrait" role="img" aria-label="Portrait photo of Dr. Kalvoric"><div></div></div>

<div class="abs svc" style="left:159px;top:328px">
  <svg width="40" height="40" viewBox="0 0 40 40" fill="#fff" aria-hidden="true"><path d="M20 8c-2-3-6-2-6 1 0 3 6 6 6 6s6-3 6-6c0-3-4-4-6-1z"/><circle cx="13" cy="20" r="2.5"/><circle cx="27" cy="18" r="2.5"/><rect x="11" y="23" width="4" height="10" rx="1"/><path d="M24 22h6l2 8h-10z"/></svg>
</div>
<div class="abs svc gold" style="left:232px;top:418px">
  <svg width="40" height="40" viewBox="0 0 40 40" fill="none" stroke="#fff" stroke-width="1.6" aria-hidden="true"><circle cx="15" cy="13" r="5"/><circle cx="26" cy="11" r="5"/><path d="M6 34v-6c0-5 4-8 9-8s9 3 9 8v6M20 18c2-1 4-2 6-2 5 0 9 3 9 8v10"/></svg>
</div>
<div class="abs svc" style="left:341px;top:461px">
  <svg width="40" height="40" viewBox="0 0 40 40" fill="#fff" aria-hidden="true"><path d="M11 24a6 6 0 0 1 2-11 8 8 0 0 1 15 1 5 5 0 0 1 1 10z"/><path d="M15 28l-1 4M21 28l-1 4M27 28l-1 4" stroke="#fff" stroke-width="1.6"/></svg>
</div>
<div class="abs svc" style="left:450px;top:418px">
  <svg width="40" height="40" viewBox="0 0 40 40" fill="#fff" aria-hidden="true"><ellipse cx="15" cy="17" rx="8" ry="10"/><ellipse cx="26" cy="23" rx="8" ry="10" fill="#fff" stroke="#8e8e8e" stroke-width="1.5"/></svg>
</div>
<div class="abs svc" style="left:523px;top:328px">
  <svg width="40" height="40" viewBox="0 0 40 40" fill="none" stroke="#fff" stroke-width="1.8" aria-hidden="true"><circle cx="20" cy="20" r="12"/><path d="M8 20a12 12 0 0 1 4-9l-1 4M32 20a12 12 0 0 1-4 9l1-4"/><circle cx="20" cy="17" r="4" fill="#fff"/><path d="M13 28c1-4 4-6 7-6s6 2 7 6" fill="#fff"/></svg>
</div>

<p class="abs svc-label right" style="right:613px;top:359px">Dating, Marriage</p>
<p class="abs svc-label right" style="right:538px;top:444px">Parenting &amp; Professional<br>Relationship</p>
<p class="abs svc-label" style="left:281px;width:200px;top:548px;text-align:center">Depression &amp;<br>Anxiety Issues</p>
<p class="abs svc-label" style="left:538px;top:455px">Personality Disorders</p>
<p class="abs svc-label" style="left:610px;top:356px">Life Management</p>

<h2 class="abs about-title">About <span>Dr. Mara L. Kalvoric</span></h2>
<p class="abs about-text">I'm so glad you are here.&nbsp; Choosing to see a professional for issues in your life can be difficult but also possibly life changing.&nbsp; Many postpone seeking help because they believe doing so acknowledges failure on their part.&nbsp; Reallly?&nbsp; We seek the help of experts all the time (contractors, mechanics, chefs, etc...) and what is more important than your life? Consulting with a neutral party to act in your best interest can be time well spent.&nbsp; So if you are willing to take the time to invest in counseling, make sure that it is with someone that is worth your time.</p>
<p class="abs read-more">READ MORE &gt;&gt;</p>

<div class="abs audio" style="top:782px">
  <div class="photo" role="img" aria-label="Photo of Dr. Kalvoric"></div>
  <span class="play"></span>
  <span class="by">Dr. Mara L. Kalvoric</span>
  <span class="title">Lorem ipsum is simply dummy text ever</span>
  <span class="wave"></span><span class="time">7:05</span>
  <span class="plays">▶ 297</span>
</div>
<div class="abs audio" style="top:888px">
  <div class="photo" role="img" aria-label="Photo of Dr. Kalvoric"></div>
  <span class="play"></span>
  <span class="by">Dr. Mara L. Kalvoric</span>
  <span class="title">Lorem ipsum is simply dummy text ever</span>
  <span class="wave"></span><span class="time">7:05</span>
  <span class="plays">▶ 297</span>
</div>

<div class="abs monitor"></div>
<div class="abs screen" role="img" aria-label="Video still of a smiling patient giving a thumbs up"></div>
<svg class="abs" style="left:547px;top:831px" width="64" height="64" viewBox="0 0 64 64" aria-hidden="true"><circle cx="32" cy="32" r="30" fill="none" stroke="#fff" stroke-width="2.5"/><path d="M26 21l17 11-17 11z" fill="#fff"/></svg>
<div class="abs chin"></div>
<div class="abs stand"></div>

<footer class="abs footer"></footer>
<h3 class="abs f-head" style="left:50px;top:1034px">Expertise</h3>
<ul class="abs f-list" style="left:50px;top:1056px">
  <li>. Dating &amp; Marriage</li>
  <li>. Parenting &amp; Professional Relationships</li>
  <li>. Depressions &amp; Anxiety Issues</li>
  <li>. Personality Disorders</li>
  <li>. Life Management</li>
</ul>
<h3 class="abs f-head" style="left:278px;top:1034px">Contact Info</h3>
<svg class="abs" style="left:275px;top:1061px" width="14" height="18" viewBox="0 0 14 18" fill="none" stroke="#bbb" stroke-width="1.2" aria-hidden="true"><path d="M7 17s6-6 6-10A6 6 0 0 0 1 7c0 4 6 10 6 10z"/><circle cx="7" cy="7" r="2"/></svg>
<p class="abs f-contact" style="left:297px;top:1059px">418 Heron Lane, Suite 120<br>Bayview, CA 92001</p>
<svg class="abs" style="left:276px;top:1099px" width="14" height="14" viewBox="0 0 14 14" fill="none" stroke="#bbb" stroke-width="1.2" aria-hidden="true"><path d="M2 1h3l1 3-2 1a8 8 0 0 0 5 5l1-2 3 1v3c-6 0-11-5-11-11z"/></svg>
<p class="abs f-contact" style="left:297px;top:1099px">(555) 014 2290</p>
<svg class="abs" style="left:275px;top:1127px" width="14" height="11" viewBox="0 0 14 11" fill="none" stroke="#bbb" stroke-width="1.2" aria-hidden="true"><rect x="1" y="1" width="12" height="9"/><path d="M1 1l6 5 6-5"/></svg>
<p class="abs f-contact" style="left:297px;top:1125px">mk@drkalvoric.com</p>
<h3 class="abs f-head" style="left:506px;top:1034px">Donation</h3>
<div class="abs badge" style="left:502px;top:1060px;width:78px;height:42px"></div>
<div class="abs badge" style="left:594px;top:1064px;width:100px;height:34px"></div>

<div class="abs rule"></div>
<p class="abs copy">© <span>drkalvoric</span> - 2016. All Rights Reserved.</p>
<p class="abs social"><span>Friendora</span><span>Chirply</span><span>Plusly</span></p>

</body>
</html>
```